Veldmark Supplies Business Card

Professional business card that stand out to our potential customers. Front and back with clean modern design

Industry/Entity Type

Oil and gas

Contact Information for Business Card

Name, address, website , office phone and cell number

Requirements
Must have
• Editable files for each employee

```html
<!DOCTYPE html>
<html lang="en">
<head>
<meta charset="utf-8">
<title>Veldmark Supplies Business Card</title>
<link href="https://fonts.googleapis.com/css2?family=Arimo:wght@400;700&display=swap" rel="stylesheet">
<style>
  :root {
    --stage: #2e2e2e;
    --card-white: #ffffff;
    --brand-red: #ff0000;
    --brand-cyan: #14a9cc;
    --back-black: #262626;
    --back-pattern: #1c1c1c;
    --text-white: #ffffff;
  }
  html, body {
    margin: 0;
    padding: 0;
    width: 1200px;
    height: 689px;
    overflow: hidden;
    background: var(--stage);
    font-family: "Arimo", Arial, sans-serif;
  }
  .canvas {
    position: relative;
    width: 1200px;
    height: 689px;
  }
  .card {
    position: absolute;
    top: 190px;
    width: 540px;
    height: 309px;
    border-radius: 16px;
    overflow: hidden;
    box-shadow: 0 10px 30px rgba(0,0,0,0.45);
  }
  .card-back {
    left: 40px;
    background: var(--back-black);
  }
  .back-pattern {
    position: absolute;
    inset: 0;
    background: linear-gradient(135deg, var(--back-pattern), var(--back-black) 60%, var(--back-pattern));
  }
  .back-mark {
    position: absolute;
    top: 26px;
    right: 30px;
    width: 14px;
    height: 14px;
    background: var(--brand-red);
  }
  .card-front {
    left: 620px;
    background: var(--card-white);
  }
  .front-bands {
    position: absolute;
    inset: 0;
  }
  .brand {
    position: absolute;
    left: 40px;
    top: 142px;
    display: flex;
    align-items: center;
    gap: 10px;
  }
  .brand-square {
    width: 18px;
    height: 18px;
    background: var(--brand-red);
  }
  .brand-name {
    font-weight: 700;
    font-size: 21px;
    letter-spacing: 0.5px;
    color: var(--brand-red);
    text-transform: uppercase;
  }
  .contact {
    position: absolute;
    right: 24px;
    top: 40px;
    text-align: right;
    color: var(--text-white);
    font-size: 12px;
    line-height: 1.45;
  }
  .person-name {
    font-weight: 700;
    font-size: 24px;
    color: var(--brand-cyan);
    line-height: 1.1;
  }
  .person-title {
    font-size: 12px;
    margin-bottom: 22px;
  }
  .address { margin-bottom: 14px; }
  .contact-line {
    display: flex;
    justify-content: flex-end;
    align-items: center;
    gap: 6px;
  }
  .contact-icon {
    width: 11px;
    height: 11px;
    fill: none;
    stroke: var(--brand-cyan);
    stroke-width: 1.6;
  }
</style>
</head>
<body>
<div class="canvas">

  <section class="card card-back" aria-label="Card back">
    <div class="back-pattern" role="img" aria-label="Repeating tone-on-tone brand mark pattern on black"></div>
    <div class="back-mark"></div>
  </section>

  <section class="card card-front" aria-label="Card front">
    <svg class="front-bands" width="540" height="309" viewBox="0 0 540 309" aria-hidden="true">
      <polygon points="322,0 328,0 302,309 288,309" fill="var(--brand-cyan)"/>
      <polygon points="333,0 540,0 540,309 311,309" fill="var(--brand-red)"/>
    </svg>

    <div class="brand">
      <span class="brand-square"></span>
      <span class="brand-name">Veldmark Supplies</span>
    </div>

    <div class="contact">
      <div class="person-name">Dale Harrow</div>
      <div class="person-title">President</div>
      <div class="address">4120 Mesa Ridge Road<br>Odessa, Texas 79761</div>
      <div class="contact-line">555-210-4871
        <svg class="contact-icon" viewBox="0 0 12 12"><path d="M3 1 L5 3.5 L4 5 Q5.5 7 7 8 L8.5 7 L11 9 L9.5 11 Q4 10 1 3 Z"/></svg>
      </div>
      <div class="contact-line">555-390-6125
        <svg class="contact-icon" viewBox="0 0 12 12"><rect x="3" y="1" width="6" height="10" rx="1"/></svg>
      </div>
      <div class="contact-line">info@veldmarksupplies.com
        <svg class="contact-icon" viewBox="0 0 12 12"><rect x="1" y="2.5" width="10" height="7"/><path d="M1 2.5 L6 6.5 L11 2.5"/></svg>
      </div>
      <div class="contact-line">www.veldmarksupplies.com
        <svg class="contact-icon" viewBox="0 0 12 12"><circle cx="6" cy="6" r="5"/><path d="M1 6 H11 M6 1 Q3 6 6 11 Q9 6 6 1"/></svg>
      </div>
    </div>
  </section>

</div>
</body>
</html>
```